Brightway Haus Inc. Business Card Design

Brightway Haus Inc. is in search of a great clean design for our business cards!

Looking to incorporate our full logo and watermark on side one (however, I am open to having the text and watermark separated within the design.)

On side two, I am looking to have contact information (Name, Position, Phone #, Email, Website (www.thebrightwayhaus.ca). Can have the logo and/or watermark as part of the design if applicable.

Please add tagline "Where Shine Counts" on either side 1 or 2. This tagline can be in a sans serif, serif or cursive font as long as it compliments overall design. Capitalization can be title or sentence case depending on how it fits within the design.

Get creative!! Looking for a clean, crisp, premium design! Looking for a glossy card finish with spot UV features when printed. Cards will also be printed with rounded corners. Standard dimensions (3.5 x 2).

Target Market(s)

B2B - primary clients are business owners or property management corporations. (residential jobs are few and far between)

Industry/Entity Type

Business

Contact Information for Business Card

- clean, crisp design
- double sided
- spot UV accents and glossy finish upon printing
- standard business card size (3.5 x 2) with rounded corners
- please see project description for requirements per side

Font styles to use
Sans Serif

Requirements
Must have
• - adequate bleeds with print ready files
• - cohesive design elements between side 1 & 2
• - spot UV elements (can be on both sides or just one, use your discretion)
• - colour pallet should match the logo file provided
• - incorporate tagline "where shine counts" (this tagline can be in a serif or sans serif font as long as it is complimentary to the overall design.
Nice to have
• - Premium elements with a clean design
Should not have
• - Please omit cartoon or whimsical like designs, think premium.
• - Colours should not stray from the pallet of the provided logo.

```html
<!DOCTYPE html>
<html lang="en">
<head>
<meta charset="utf-8">
<title>Brightway Haus Inc. Business Card</title>
<link href="https://fonts.googleapis.com/css2?family=Open+Sans:wght@700&family=Roboto:wght@400;500&family=Roboto+Condensed:wght@500&display=swap" rel="stylesheet">
<style>
  :root {
    --backdrop: #ece9e4;
    --card-dark: #1d1e20;
    --card-light: #f4f4f4;
    --teal: #10b7bd;
    --navy: #1b2455;
    --grey-text: #555a5e;
    --white: #ffffff;
  }
  html, body {
    margin: 0;
    width: 1200px;
    height: 960px;
    overflow: hidden;
    background: var(--backdrop);
  }
  .canvas { position: relative; width: 1200px; height: 960px; }
  .card {
    position: absolute;
    width: 600px;
    height: 343px;
    border-radius: 22px;
    overflow: hidden;
  }
  .card-front { left: 320px; top: 108px; background: var(--card-dark); }
  .card-back { left: 320px; top: 492px; background: var(--card-light); }

  .front-wordmark {
    position: absolute; left: 0; right: 0; top: 134px;
    text-align: center;
    font: 700 46px/1 "Open Sans", sans-serif;
    letter-spacing: -0.5px;
    color: var(--teal);
  }
  .front-tagline {
    position: absolute; left: 0; right: 0; top: 194px;
    text-align: center;
    font: 400 16px/1 "Roboto", sans-serif;
    letter-spacing: 7px;
    color: var(--white);
  }

  .back-accent { position: absolute; inset: 0; }
  .back-wordmark {
    position: absolute; left: 28px; top: 36px;
    font: 700 27px/1 "Open Sans", sans-serif;
    letter-spacing: -0.5px;
    color: var(--teal);
  }
  .contact-block { position: absolute; left: 28px; top: 120px; }
  .person-name {
    margin: 0;
    font: 500 21px/1 "Roboto Condensed", sans-serif;
    color: var(--teal);
  }
  .person-role {
    margin: 8px 0 0;
    font: 500 15px/1 "Roboto", sans-serif;
    color: var(--navy);
  }
  .address {
    margin: 14px 0 0;
    font: 400 14px/19px "Roboto", sans-serif;
    color: var(--grey-text);
  }
  .contact-list { list-style: none; margin: 12px 0 0; padding: 0; }
  .contact-list li {
    display: flex; align-items: center; gap: 9px;
    font: 400 14px/19px "Roboto", sans-serif;
    color: var(--grey-text);
  }
  .contact-icon { width: 13px; height: 13px; fill: var(--teal); flex: none; }
</style>
</head>
<body>
<main class="canvas">
  <section class="card card-front" aria-label="Card front">
    <div class="front-wordmark">BRIGHTWAY HAUS INC.</div>
    <div class="front-tagline">Where Shine Counts</div>
  </section>

  <section class="card card-back" aria-label="Card back">
    <svg class="back-accent" viewBox="0 0 600 343" width="600" height="343" aria-hidden="true">
      <path d="M340 0 H600 V168 C470 205 360 245 300 270 C320 180 330 90 340 0 Z" fill="var(--teal)"/>
      <path d="M262 262 C360 268 480 230 600 188 V343 H282 C270 320 262 290 262 262 Z" fill="var(--navy)"/>
    </svg>

    <div class="back-wordmark">BRIGHTWAY HAUS INC.</div>

    <div class="contact-block">
      <h1 class="person-name">DANIEL REEVE</h1>
      <p class="person-role">CEO/FOUNDER</p>
      <p class="address">2190 Alder Crescent<br>Halifax, Nova Scotia 48213</p>
      <ul class="contact-list">
        <li><svg class="contact-icon" viewBox="0 0 16 16"><path d="M3.6 1.2l2.3 2.6-1.3 2c.9 2 2.6 3.7 4.6 4.6l2-1.3 2.6 2.3-1.4 2.6C7 13.6 2.4 9 1 3z"/></svg>555 214 7730</li>
        <li><svg class="contact-icon" viewBox="0 0 16 16"><path d="M4 0h8a1 1 0 011 1v14a1 1 0 01-1 1H4a1 1 0 01-1-1V1a1 1 0 011-1zm1 2v10h6V2zm3 11a1 1 0 100 2 1 1 0 000-2z"/></svg>555 308 4126</li>
        <li><svg class="contact-icon" viewBox="0 0 16 16"><path d="M4 1h8v4H4zM1 6h14v7h-3v2H4v-2H1zm4 5v3h6v-3z"/></svg>555 917 2085</li>
        <li><svg class="contact-icon" viewBox="0 0 16 16"><path d="M1 3h14v1L8 9 1 4zm0 3l7 5 7-5v7H1z"/></svg>hello@thebrightwayhaus.ca</li>
        <li><svg class="contact-icon" viewBox="0 0 16 16"><path d="M8 0a8 8 0 110 16A8 8 0 018 0zm0 1.5a6.5 6.5 0 00-5.6 9.8L6 9l1-3 3-1 1.5-2A6.5 6.5 0 008 1.5zm3 8l-2 2 1 3a6.5 6.5 0 004-5z"/></svg>www.thebrightwayhaus.ca</li>
      </ul>
    </div>
  </section>
</main>
</body>
</html>
```